The Plate Compass

Cutting Through the Noise to What Actually Works.

Nutrition book

Target Market(s)

People looking to be or get healthy and eat right.

```html
<!DOCTYPE html>
<html lang="en">
<head>
<meta charset="UTF-8">
<title>The Plate Compass — Book Cover</title>
<link rel="stylesheet" href="https://fonts.googleapis.com/css2?family=Playfair+Display:wght@700;800&family=Poppins:wght@600;700&display=swap">
<style>
  :root {
    --backdrop: #9a9a9a;
    --paper: #ece6da;
    --olive-dark: #4a5a24;
    --olive-light: #869456;
    --charcoal: #3c3c3c;
    --ink: #111111;
    --rule: #a9b083;
    --arc-green: #3d7d2c;
    --plate-white: #f4f3ef;
  }
  * { margin: 0; padding: 0; box-sizing: border-box; }
  html, body {
    width: 1200px; height: 1192px; overflow: hidden;
    background: var(--backdrop);
  }
  .cover {
    position: absolute; left: 246px; top: 65px;
    width: 708px; height: 1062px;
    background: var(--paper);
    overflow: hidden;
  }
  .title-kicker {
    position: absolute; top: 66px; left: 0; width: 100%;
    display: flex; align-items: center; justify-content: center; gap: 12px;
    font-family: "Playfair Display", serif; font-weight: 700;
    font-size: 70px; line-height: 1; color: var(--olive-dark);
  }
  .title-kicker .rule { width: 128px; height: 2px; background: var(--rule); }
  .title-main {
    position: absolute; left: 0; width: 100%; text-align: center;
    font-family: "Playfair Display", serif; font-weight: 800;
    font-size: 132px; line-height: 1; letter-spacing: -1px;
  }
  .title-main.line-one { top: 118px; color: var(--olive-dark); }
  .title-main.line-two { top: 224px; color: var(--charcoal); }
  .subtitle {
    position: absolute; top: 353px; left: 0; width: 100%; text-align: center;
    font-family: "Poppins", sans-serif; font-weight: 600;
    font-size: 28px; line-height: 39px; color: var(--ink);
  }
  .leaf-sprig {
    position: absolute; left: 617px; top: 361px; width: 91px; height: 162px;
    background: linear-gradient(160deg, rgba(140,170,80,0.55), rgba(170,195,110,0.25));
    border-radius: 60% 0 0 60%;
  }
  .hierarchy-chart { position: absolute; left: 0; top: 0; width: 708px; height: 1062px; }
  .hierarchy-chart .bar-label {
    font-family: "Poppins", sans-serif; font-weight: 700; font-size: 23px; fill: #ffffff;
  }
  .author {
    position: absolute; top: 953px; left: 0; width: 100%;
    display: flex; align-items: center; justify-content: center; gap: 12px;
    font-family: "Playfair Display", serif; font-weight: 700;
    font-size: 40px; line-height: 1; color: var(--olive-dark); letter-spacing: 1px;
  }
  .author .rule { width: 74px; height: 2px; background: var(--rule); }
</style>
</head>
<body>
  <main class="cover">
    <div class="title-kicker"><span class="rule"></span><span>THE</span><span class="rule"></span></div>
    <h1 class="title-main line-one">PLATE</h1>
    <div class="title-main line-two">COMPASS</div>
    <p class="subtitle">Cutting Through the Noise to<br>What Actually Works</p>

    <div class="leaf-sprig" role="img" aria-label="Watercolour sprig of green leaves"></div>

    <svg class="hierarchy-chart" viewBox="0 0 708 1062" aria-label="Nutrition priorities from noise to calories">
      <g class="bars">
        <polygon points="150,475 526,475 489,538 150,538" fill="var(--olive-light)"/>
        <polygon points="150,546 606,546 568,609 150,609" fill="var(--olive-dark)"/>
        <polygon points="150,618 635,618 597,681 150,681" fill="var(--olive-light)"/>
        <polygon points="150,691 662,691 624,754 150,754" fill="var(--olive-dark)"/>
        <polygon points="150,763 690,763 652,826 150,826" fill="var(--olive-light)"/>
        <polygon points="150,837 708,837 670,901 150,901" fill="var(--olive-dark)"/>
      </g>
      <circle cx="165" cy="688" r="232" fill="var(--paper)"/>
      <g class="ring">
        <path d="M165 464 A224 224 0 0 1 273.6 492 L264.4 508.6 A205 205 0 0 0 165 483 Z" fill="var(--olive-light)"/>
        <path d="M280.4 496 A224 224 0 0 1 357 572.6 L340.7 582.4 A205 205 0 0 0 270.6 512.3 Z" fill="var(--olive-dark)"/>
        <path d="M361 579.4 A224 224 0 0 1 389 684.2 L370 684.5 A205 205 0 0 0 344.4 588.6 Z" fill="var(--olive-light)"/>
        <path d="M389 691.8 A224 224 0 0 1 361 796.6 L344.4 787.4 A205 205 0 0 0 370 691.5 Z" fill="var(--olive-dark)"/>
        <path d="M357 803.4 A224 224 0 0 1 280.4 880 L270.6 863.7 A205 205 0 0 0 340.7 793.6 Z" fill="var(--olive-light)"/>
        <path d="M273.6 884 A224 224 0 0 1 165 912 L165 893 A205 205 0 0 0 264.4 867.4 Z" fill="var(--olive-dark)"/>
      </g>
      <path d="M160 476 A212 212 0 0 0 160 900" fill="none" stroke="var(--arc-green)" stroke-width="2"/>
      <circle cx="165" cy="688" r="166" fill="var(--plate-white)" stroke="#e2e0da" stroke-width="3"/>
      <circle cx="165" cy="688" r="150" fill="#c98a52" opacity="0.55" role="img" aria-label="Photo of a plate with vegetables, fruit, cheese, bread, meat and legumes"/>
      <g class="labels">
        <text class="bar-label" x="326" y="515">Noise</text>
        <text class="bar-label" x="375" y="586">Supplements</text>
        <text class="bar-label" x="395" y="658">Meal timing</text>
        <text class="bar-label" x="402" y="731">Food quality</text>
        <text class="bar-label" x="384" y="803">Protein</text>
        <text class="bar-label" x="332" y="877">Calories</text>
      </g>
    </svg>

    <div class="author"><span class="rule"></span><span>MARTIN HALE</span><span class="rule"></span></div>
  </main>
</body>
</html>
```